Kestrel Facilities Business Card Design

We would now like to design business cards with the new Kestrel Facilities logo

Target Market(s)

Professional

Industry/Entity Type

Professional services

Contact Information for Business Card

Employee name, title, phone number, email address, corporate office address and logo.

Font styles to use
Sans Serif

Colors
0054AA
0677BA
7BADD7
CADEEF
E8F1F8

Requirements
Must have
• My logo
Should not have
• any other pictures or images besides my logo

```html
<!DOCTYPE html>
<html lang="en">
<head>
<meta charset="utf-8">
<title>Kestrel Facilities Business Card</title>
<link href="https://fonts.googleapis.com/css2?family=Montserrat:wght@400;500;700&display=swap" rel="stylesheet">
<style>
  :root {
    --brand-blue: #3679bf;
    --ink: #1a1a1a;
    --card-white: #ffffff;
    --backdrop: #8f8f8f;
    --backdrop-light: #c4c4c4;
  }
  html, body {
    margin: 0;
    padding: 0;
    width: 1200px;
    height: 900px;
    overflow: hidden;
  }
  body {
    background: radial-gradient(ellipse at 45% 45%, var(--backdrop-light), var(--backdrop) 75%);
    font-family: "Montserrat", sans-serif;
    position: relative;
  }
  .card {
    position: absolute;
    width: 630px;
    height: 360px;
    background: var(--card-white);
    border-radius: 28px;
    overflow: hidden;
    box-shadow: 0 10px 24px rgba(0,0,0,0.28);
  }
  .card-back { left: 80px; top: 50px; }
  .card-front { left: 490px; top: 480px; }

  .brand-name {
    position: absolute;
    color: var(--brand-blue);
    font-weight: 700;
    letter-spacing: 0.02em;
    display: flex;
    align-items: center;
    gap: 14px;
    white-space: nowrap;
  }
  .brand-mark {
    display: inline-block;
    background: var(--brand-blue);
  }
  .card-back .brand-name {
    left: 0; right: 0; top: 0; bottom: 0;
    justify-content: center;
    font-size: 40px;
  }
  .card-back .brand-mark { width: 34px; height: 34px; }

  .front-wave {
    position: absolute;
    left: 0; top: 0;
    width: 630px; height: 360px;
  }
  .card-front .brand-name {
    right: 30px;
    top: 212px;
    font-size: 26px;
    gap: 10px;
  }
  .card-front .brand-mark { width: 24px; height: 24px; }

  .contact-block {
    position: absolute;
    left: 64px;
    top: 128px;
    color: var(--ink);
  }
  .person-name {
    margin: 0;
    font-size: 22px;
    line-height: 1.2;
    font-weight: 700;
    color: var(--brand-blue);
    letter-spacing: 0.01em;
  }
  .person-title {
    margin: 2px 0 14px;
    font-size: 15px;
    font-weight: 500;
  }
  .address {
    margin: 0 0 12px;
    font-size: 14px;
    line-height: 1.35;
    font-style: normal;
  }
  .contact-list {
    list-style: none;
    margin: 0;
    padding: 0;
    font-size: 14px;
    line-height: 1.5;
  }
  .contact-list li {
    display: flex;
    align-items: center;
    gap: 8px;
  }
  .contact-icon {
    width: 13px;
    height: 13px;
    fill: var(--brand-blue);
    flex: none;
  }
</style>
</head>
<body>

<section class="card card-back" aria-label="Business card back">
  <div class="brand-name"><span class="brand-mark"></span>Kestrel Facilities</div>
</section>

<section class="card card-front" aria-label="Business card front">
  <svg class="front-wave" viewBox="0 0 630 360" aria-hidden="true">
    <path class="wave-main" fill="var(--brand-blue)"
      d="M0,0 H630 V96 C575,110 470,78 340,56 C220,36 90,22 0,48 Z"/>
    <path class="wave-swoosh" fill="var(--brand-blue)"
      d="M0,66 C80,46 200,54 330,64 C210,66 100,76 42,102 C25,112 10,124 0,136 Z"/>
  </svg>

  <div class="brand-name"><span class="brand-mark"></span>Kestrel Facilities</div>

  <div class="contact-block">
    <h1 class="person-name">DARA WHITCOMBE</h1>
    <p class="person-title">Co-Founder</p>
    <address class="address">1180 W. Harbor Lane<br>Suite 402 Northgate.14</address>
    <ul class="contact-list">
      <li>
        <svg class="contact-icon" viewBox="0 0 16 16"><path d="M3 1h3l1.5 4-2 1.3a9 9 0 0 0 4.2 4.2L11 8.5l4 1.5v3a2 2 0 0 1-2 2A13 13 0 0 1 1 3a2 2 0 0 1 2-2z"/></svg>
        +254-700-41532
      </li>
      <li>
        <svg class="contact-icon" viewBox="0 0 16 16"><path d="M1 3h14v10H1z M1.8 3.6 8 8.6l6.2-5" stroke="#fff" stroke-width="1.2"/></svg>
        hello@kestrelfm.com
      </li>
      <li>
        <svg class="contact-icon" viewBox="0 0 16 16"><circle cx="8" cy="8" r="7"/><path d="M1 8h14M8 1c3 3 3 11 0 14M8 1c-3 3-3 11 0 14" stroke="#fff" stroke-width="1" fill="none"/></svg>
        www.kestrelfm.com
      </li>
    </ul>
  </div>
</section>

</body>
</html>
```